Business Card Design Project - del varosi group

dear Sirs

we need business card design for our group ( DEL Varosi Group ) , i have got the Logo design of our group from pixel harbor in previous , so all need details relating to our group i think available with you, as well as the the chosen logo design

we hope to provide us with business card logo that to be appropaite and satisfactory to us .

thanks

note : logo design of our group is attached .
Updates

Reason: please extend the deadline of my project for additional 15 days because i didn't received appropriate design for our gruop yet . kindly beaware that i have received 77 design till now , supossed to send me 200-250 design at least . thanks

Target Market(s)

contents

name : Kerem EL Nadiri

position : Operation Manager

Industry/Entity Type

Business

Requirements
Must have

• person name

group logo
Nice to have
• logo color matching with back background

```html
<!DOCTYPE html>
<html lang="en">
<head>
<meta charset="utf-8">
<title>DEL Varosi Group – Business Card</title>
<link href="https://fonts.googleapis.com/css2?family=Lato:wght@400;700&display=swap" rel="stylesheet">
<style>
  :root {
    --brand-blue: #0b47a8;
    --brand-blue-dark: #083a8c;
    --card-white: #f4f5f6;
    --ink: #2a2a2a;
    --page-bg: #e6e6e4;
  }
  * { box-sizing: border-box; margin: 0; padding: 0; }
  html, body {
    width: 1200px; height: 720px; overflow: hidden;
    background: var(--page-bg);
    font-family: "Lato", sans-serif;
  }
  .canvas {
    position: relative; width: 1200px; height: 720px;
    display: flex; align-items: center; justify-content: center; gap: 40px;
  }
  .card {
    position: relative; width: 520px; height: 300px;
    background: var(--card-white);
    border: 14px solid var(--brand-blue);
    box-shadow: 0 6px 18px rgba(0,0,0,0.18);
    overflow: hidden;
  }
  /* Logo stand-in */
  .brand-mark { display: flex; align-items: center; gap: 8px; color: var(--brand-blue); font-weight: 700; letter-spacing: 0.5px; }
  .brand-mark .brand-square { background: var(--brand-blue); flex: none; }
  .card-front .brand-mark { position: absolute; top: 14px; right: 18px; font-size: 17px; }
  .card-front .brand-square { width: 12px; height: 12px; }
  .card-back { display: flex; align-items: center; justify-content: center; }
  .card-back .brand-mark { font-size: 40px; gap: 14px; }
  .card-back .brand-square { width: 30px; height: 30px; }

  /* Name band */
  .name-band {
    position: absolute; left: 0; top: 118px;
    width: 244px; height: 62px;
    background: var(--brand-blue); color: #fff;
    padding: 10px 0 0 22px;
  }
  .person-name { font-size: 20px; font-weight: 400; letter-spacing: 0.3px; }
  .person-role { font-size: 13px; margin-top: 2px; opacity: 0.92; }

  .online { position: absolute; left: 22px; bottom: 18px; color: var(--ink); }
  .online .email { font-size: 13px; }
  .online .website { font-size: 14px; font-weight: 700; margin-top: 4px; }

  .address { position: absolute; left: 286px; top: 92px; font-size: 12.5px; line-height: 1.45; color: var(--ink); }

  .contacts { position: absolute; left: 286px; top: 170px; list-style: none; font-size: 13.5px; color: var(--ink); }
  .contacts li { display: flex; align-items: center; gap: 10px; height: 19px; }
  .contacts svg { width: 13px; height: 13px; fill: var(--brand-blue-dark); flex: none; }
</style>
</head>
<body>
<main class="canvas">

  <section class="card card-front" aria-label="Business card front">
    <div class="brand-mark"><span class="brand-square"></span><span>DEL VAROSI GROUP</span></div>

    <div class="name-band">
      <p class="person-name">Kerem EL Nadiri</p>
      <p class="person-role">Operation Manager</p>
    </div>

    <address class="address" style="font-style:normal">
      Rue Carnot - Plateau<br>
      BP 512 - Dakar, Sénégal
    </address>

    <ul class="contacts">
      <li>
        <svg viewBox="0 0 16 16" aria-label="Telephone"><rect x="1" y="5" width="14" height="10" rx="1.5"/><rect x="3" y="1" width="10" height="4" rx="1"/></svg>
        (221) 33 841 20 15
      </li>
      <li>
        <svg viewBox="0 0 16 16" aria-label="Fax"><rect x="4" y="1" width="8" height="4"/><rect x="1" y="6" width="14" height="6" rx="1"/><rect x="4" y="11" width="8" height="4"/></svg>
        (221) 33 841 20 16
      </li>
      <li>
        <svg viewBox="0 0 16 16" aria-label="Mobile"><rect x="4" y="0.5" width="8" height="15" rx="1.5"/><rect x="5.5" y="2.5" width="5" height="9" fill="#f4f5f6"/></svg>
        (221) 77 402 58 31
      </li>
    </ul>

    <div class="online">
      <p class="email">kerem-nadiri@del-varosi.com</p>
      <p class="website">www.del-varosi.com</p>
    </div>
  </section>

  <section class="card card-back" aria-label="Business card back">
    <div class="brand-mark"><span class="brand-square"></span><span>DEL VAROSI GROUP</span></div>
  </section>

</main>
</body>
</html>
```